Need App for Impact Related Events

My app is to help with internal events. When you enter the prompted event code the next screen shows you everyone currently at the event. It will give you the ability to Start a conversation with someone you met at that event, or signal it is your turn to send a message. The next screen is a message thread with that person. I am looking for a design that incorporates the colors and ‘feel good’ emotion of our logo. I have pieced together a pretty good interpretation of what I’m looking for in the attached mockup by slicing and dicing designs. I also attached our logo mascot.Screens (see attached mockups)

Note 1: I do not like the picture on the screen used in screen one because it makes it seem like a dating app. I attached an alternative photo that can be used or present different ideas.

Note 2: On the login/signup screen (screen 2) I need an additional first and last name for login, you can try to fit this on one login screen or present a two step signup screen where that is presented in the second screen.

READ MOCKUP GUIDELINES UNDER Must Haves

Target Market(s)

People attending internal social impact events

Industry/Entity Type

Charity

Font styles to use
Sans Serif

Colors
86cfc6

Requirements
Must have
• Follow the screen mockups attached to project
• PLEASE READ
• I have provided a relatively close design of what I’m looking for in the mockups. Some screens need to be followed more closely to my design mockup than other. I have listed a guide below how how closely you should follow my mockup design exactly. Overall I would like to see some ideas of incorporating a few accent colors so it doesn’t appear SO Blue. I also attached some app inspiration designs I found from around the web
• Screen Mockup Guideline Follow %
• Screen 1: 65% - mostly on target, would like to see ways to make it not SO Blue and possibly creative places to add some explainer text describing the app
• Screen 2: 50% - general design idea is here, but more open
• Screen 3: 35% - a lot more room for design influence
• Screen 4: 70% - mostly on target, a little room for design influence/color scheme ideas
• Screen 5-6: 25% - a lot of room for design change/ideas/influence
• Screen 7-8: 80% - already very close to what I need, maybe open to slight sizing and color scheme ideas
• Screen 9: 15% - the most open for influence, only the general functionality of the screen is communicated here
Nice to have
• Please Read Mockup Guideline above. In large part I am looking for something to use some nice accent colors so it is not overwhelmingly blue and bring the whole design into a seamless style.
Should not have

```html
<!DOCTYPE html>
<html lang="en">
<head>
<meta charset="utf-8">
<title>Events – Enter the Code</title>
<link rel="stylesheet" href="https://fonts.googleapis.com/css2?family=Nunito:wght@400;700;800&family=Roboto:wght@400;500&display=swap">
<style>
:root{
  --screen-bg:#72e2df;
  --heading-teal:#168c89;
  --card-bg:#7de6e3;
  --card-image-a:#5e9fb4;
  --card-image-b:#8fc9cf;
  --line-soft:#9eecea;
  --modal-bg:#ffffff;
  --ink:#2a2d33;
  --muted:#6d7075;
  --field-border:#dfe3e6;
  --accent:#10c8c4;
  --kb-bg:#eef0f1;
  --kb-strip:#f3f4f5;
  --kb-key:#3c4043;
  --kb-hint:#5f6368;
  --kb-space:#d9dbdd;
  --kb-enter:#3f7ff0;
}
*{box-sizing:border-box;margin:0;padding:0}
html,body{width:675px;height:1200px;overflow:hidden}
body{font-family:"Nunito",sans-serif;background:var(--screen-bg)}
.screen{position:relative;width:675px;height:1200px;overflow:hidden;background:var(--screen-bg)}
.page-title{position:absolute;left:30px;top:34px;font-size:50px;font-weight:800;color:var(--heading-teal);letter-spacing:.5px}
.profile-avatar{position:absolute;left:582px;top:34px;width:66px;height:66px;border-radius:50%;background:radial-gradient(circle at 50% 40%,#4f8f95,#2a5f66)}
.search-bar{position:absolute;left:56px;top:141px;width:563px;height:69px;border:2px solid var(--line-soft);border-radius:6px}
.event-card{position:absolute;left:30px;top:338px;width:615px;height:460px;background:var(--card-bg);border-radius:8px;overflow:hidden}
.event-image{height:300px;background:radial-gradient(circle at 20% 40%,var(--card-image-b),var(--card-image-a) 70%)}
.event-name{position:absolute;left:18px;top:314px;font-size:37px;font-weight:800;color:var(--heading-teal)}
.event-date{position:absolute;left:20px;top:385px;font-size:24px;font-weight:700;color:#4fa8a6}
.attendees{position:absolute;left:310px;top:385px;display:flex;gap:16px}
.attendees span{width:56px;height:56px;border-radius:50%;background:#5aa5aa}
.attendees span:last-child{background:var(--accent)}
.modal{position:absolute;left:88px;top:163px;width:501px;height:488px;background:var(--modal-bg);border-radius:8px;text-align:center}
.modal-title{margin-top:28px;font-size:36px;font-weight:700;color:var(--ink)}
.code-field{display:block;margin:32px auto 0;width:450px;height:75px;border:2px solid var(--field-border);border-radius:11px;padding:0 28px;text-align:left;font:400 26px "Nunito",sans-serif;color:#8a8d92;line-height:71px}
.modal-help{margin:40px auto 0;width:440px;font-size:24px;line-height:37px;color:var(--muted)}
.enter-button{display:block;margin:60px auto 0;width:300px;height:75px;border:none;border-radius:8px;background:var(--accent);color:#fff;font:800 22px "Nunito",sans-serif;letter-spacing:2px;box-shadow:0 3px 6px rgba(0,0,0,.15)}
.keyboard{position:absolute;left:0;top:737px;width:675px;height:463px;background:var(--kb-bg);font-family:"Roboto",sans-serif;color:var(--kb-key)}
.suggestions{height:75px;background:var(--kb-strip);position:relative;font-size:28px}
.suggestions span{position:absolute;top:20px}
.suggestions .divider{position:absolute;top:20px;width:2px;height:36px;background:#c7c9cc}
.key{position:absolute;font-size:36px;transform:translateX(-50%);line-height:1}
.hint{position:absolute;font-size:16px;line-height:1;color:var(--kb-hint);transform:translateX(-50%)}
.space-bar{position:absolute;left:253px;top:388px;width:235px;height:42px;background:var(--kb-space);border-radius:4px}
.enter-key{position:absolute;left:595px;top:385px;width:48px;height:48px;border-radius:50%;background:var(--kb-enter)}
</style>
</head>
<body>
<main class="screen">
  <h1 class="page-title">Events</h1>
  <div class="profile-avatar" role="img" aria-label="Profile photo"></div>
  <div class="search-bar"></div>

  <article class="event-card">
    <div class="event-image" role="img" aria-label="Event photo with balloons"></div>
    <h2 class="event-name">Nora's Party</h2>
    <p class="event-date">22 - Sep - 2018</p>
    <div class="attendees"><span></span><span></span><span></span><span></span></div>
  </article>

  <section class="modal">
    <h2 class="modal-title">Enter the Code</h2>
    <div class="code-field">Event Code</div>
    <p class="modal-help">Please enter the Event code that you received by your friend or family</p>
    <button class="enter-button">ENTER</button>
  </section>

  <section class="keyboard">
    <div class="suggestions">
      <span style="left:115px">Hi</span>
      <i class="divider" style="left:237px"></i>
      <span style="left:297px">Hello</span>
      <i class="divider" style="left:434px"></i>
      <span style="left:476px">Howdy</span>
      <svg style="position:absolute;left:630px;top:22px" width="18" height="32" viewBox="0 0 18 32"><rect x="4" y="0" width="10" height="18" rx="5" fill="#5f6368"/><path d="M1 14a8 8 0 0 0 16 0" fill="none" stroke="#5f6368" stroke-width="2"/><rect x="8" y="22" width="2" height="8" fill="#5f6368"/></svg>
    </div>

    <span class="hint" style="left:32px;top:92px">1</span><span class="hint" style="left:100px;top:92px">2</span><span class="hint" style="left:167px;top:92px">3</span><span class="hint" style="left:235px;top:92px">4</span><span class="hint" style="left:302px;top:92px">5</span><span class="hint" style="left:370px;top:92px">6</span><span class="hint" style="left:437px;top:92px">7</span><span class="hint" style="left:505px;top:92px">8</span><span class="hint" style="left:572px;top:92px">9</span><span class="hint" style="left:640px;top:92px">0</span>

    <span class="key" style="left:32px;top:117px">q</span><span class="key" style="left:100px;top:117px">w</span><span class="key" style="left:167px;top:117px">e</span><span class="key" style="left:235px;top:117px">r</span><span class="key" style="left:302px;top:117px">t</span><span class="key" style="left:370px;top:117px">y</span><span class="key" style="left:437px;top:117px">u</span><span class="key" style="left:505px;top:117px">i</span><span class="key" style="left:572px;top:117px">o</span><span class="key" style="left:640px;top:117px">p</span>

    <span class="key" style="left:69px;top:212px">a</span><span class="key" style="left:137px;top:212px">s</span><span class="key" style="left:204px;top:212px">d</span><span class="key" style="left:272px;top:212px">f</span><span class="key" style="left:339px;top:212px">g</span><span class="key" style="left:407px;top:212px">h</span><span class="key" style="left:474px;top:212px">j</span><span class="key" style="left:542px;top:212px">k</span><span class="key" style="left:609px;top:212px">l</span>

    <svg style="position:absolute;left:36px;top:300px" width="30" height="34" viewBox="0 0 30 34"><path d="M15 2 2 16h7v8h12v-8h7z" fill="#3c4043"/><rect x="9" y="28" width="12" height="3" fill="#3c4043"/></svg>
    <span class="key" style="left:135px;top:300px">z</span><span class="key" style="left:202px;top:300px">x</span><span class="key" style="left:270px;top:300px">c</span><span class="key" style="left:337px;top:300px">v</span><span class="key" style="left:405px;top:300px">b</span><span class="key" style="left:472px;top:300px">n</span><span class="key" style="left:540px;top:300px">m</span>
    <svg style="position:absolute;left:602px;top:308px" width="38" height="26" viewBox="0 0 38 26"><path d="M10 0h28v26H10L0 13z" fill="#3c4043"/><path d="M18 7l12 12M30 7 18 19" stroke="#eef0f1" stroke-width="3"/></svg>

    <span class="key" style="left:52px;top:396px;font-size:26px">?123</span>
    <span class="key" style="left:133px;top:388px">,</span>
    <svg style="position:absolute;left:188px;top:394px" width="30" height="30" viewBox="0 0 30 30"><circle cx="15" cy="15" r="12" fill="none" stroke="#3c4043" stroke-width="2.5"/></svg>
    <div class="space-bar"></div>
    <span class="key" style="left:538px;top:388px">.</span>
    <div class="enter-key"></div>
    <svg style="position:absolute;left:606px;top:397px" width="26" height="24" viewBox="0 0 26 24"><path d="M22 2v10H5" fill="none" stroke="#fff" stroke-width="3"/><path d="M10 5 3 12l7 7" fill="none" stroke="#fff" stroke-width="3"/></svg>
  </section>
</main>
</body>
</html>
```